Business card design Needed for new logo / Construction business, home extensions and new builds

We need a business card design using our new logo files which i will attach to this project :)

We are a small construction business specialising in home extensions, new builds and property development. We are very ambitious and would appreciate professional and elegant designs for our new business card.

Very serious about using the services on MakerQuarry and recently acquired our new logo from here :)

Please get involved, i will feedback when i can as i am very busy but can respond daily, thanks

Target Market(s)

People that want to build onto their houses, new building developments or adding too their existing property

Industry/Entity Type

Construction

Contact Information for Business Card

Renwick Tolliver Construction, Lionel Ashby (Managing Director), Tel 07822254961, email - info@renwick-tolliver, www.renwick-tolliver.co.uk

Colors

Designer to choose colors to be used in the design.

Requirements
Must have
• I like a deep grey on the back please. A lot of you have provided black from and back, try mixing things up a little. The black looks cool 😎 Thanks

```html
<!DOCTYPE html>
<html lang="en">
<head>
<meta charset="utf-8">
<title>Renwick Tolliver Construction – Business Card</title>
<link href="https://fonts.googleapis.com/css2?family=Arimo:wght@400;700&display=swap" rel="stylesheet">
<style>
  :root {
    --backdrop: #1c1c1d;
    --card-dark: #303031;
    --gold-deep: #ad7423;
    --gold-mid: #c9973f;
    --gold-light: #ecc778;
    --silver-deep: #a9acb1;
    --silver-light: #eef0f2;
    --ink: #111111;
    --text-light: #f2f2f2;
    --text-soft: #d6d6d6;
    --web-ink: #3a3b3d;
  }
  * { margin: 0; padding: 0; box-sizing: border-box; }
  html, body {
    width: 1200px; height: 960px; overflow: hidden;
    background: var(--backdrop);
    font-family: "Arimo", Arial, sans-serif;
  }
  .canvas {
    width: 1200px; height: 960px;
    display: flex; flex-direction: column;
    align-items: center; justify-content: center; gap: 40px;
  }
  .card {
    position: relative;
    width: 735px; height: 420px;
    border-radius: 24px;
    overflow: hidden;
  }
  /* Front */
  .card-front {
    background: radial-gradient(ellipse at 50% 40%, var(--gold-light) 0%, var(--gold-mid) 50%, var(--gold-deep) 100%);
    display: flex; align-items: center; justify-content: center;
  }
  .brand {
    display: flex; align-items: center; gap: 16px;
    color: var(--ink);
    font-weight: 700;
  }
  .brand-mark { width: 22px; height: 22px; background: var(--ink); }
  .brand-name { font-size: 30px; letter-spacing: 2px; text-transform: uppercase; line-height: 1.25; text-align: center; }
  /* Back */
  .card-back { background: var(--card-dark); }
  .bands { position: absolute; inset: 0; }
  .contact-person { position: absolute; left: 52px; top: 190px; }
  .person-name { color: var(--gold-mid); font-weight: 700; font-size: 30px; }
  .person-role { color: var(--text-soft); font-size: 19px; margin-top: 4px; }
  .divider {
    position: absolute; left: 52px; right: 48px; top: 268px;
    height: 1px; background: var(--text-soft); opacity: .7;
  }
  .phone {
    position: absolute; left: 52px; top: 280px;
    display: flex; align-items: center; gap: 10px;
    color: var(--text-light); font-size: 20px;
  }
  .email {
    position: absolute; right: 48px; top: 236px;
    display: flex; align-items: center; gap: 12px;
    color: var(--text-light); font-size: 20px;
  }
  .brand-back {
    position: absolute; right: 56px; top: 86px;
    color: var(--gold-mid);
    font-size: 24px;
  }
  .brand-back .brand-mark { background: var(--gold-mid); width: 18px; height: 18px; }
  .website {
    position: absolute; right: 48px; top: 372px;
    color: var(--web-ink); font-size: 20px;
  }
</style>
</head>
<body>
<main class="canvas">
  <section class="card card-front">
    <div class="brand">
      <span class="brand-mark"></span>
      <span class="brand-name">Renwick Tolliver<br>Construction</span>
    </div>
  </section>

  <section class="card card-back">
    <svg class="bands" viewBox="0 0 735 420" preserveAspectRatio="none">
      <defs>
        <linearGradient id="goldBand" x1="0" x2="1" y1="0" y2="0">
          <stop offset="0" stop-color="#ad7423"/>
          <stop offset=".55" stop-color="#ecc778"/>
          <stop offset="1" stop-color="#b07826"/>
        </linearGradient>
        <linearGradient id="silverBand" x1="0" x2="1" y1="0" y2="1">
          <stop offset="0" stop-color="#a9acb1"/>
          <stop offset=".5" stop-color="#eef0f2"/>
          <stop offset="1" stop-color="#b5b8bd"/>
        </linearGradient>
      </defs>
      <polygon points="0,348 325,348 355,330 735,330 735,420 0,420" fill="url(#silverBand)"/>
      <polygon points="0,318 345,318 325,348 0,348" fill="url(#goldBand)"/>
    </svg>

    <div class="brand brand-back">
      <span class="brand-mark"></span>
      <span class="brand-name">Renwick Tolliver<br>Construction</span>
    </div>

    <div class="contact-person">
      <p class="person-name">Lionel Ashby</p>
      <p class="person-role">Managing Director</p>
    </div>

    <div class="email">
      <span>info@renwick-tolliver</span>
      <svg width="20" height="14" viewBox="0 0 20 14" aria-hidden="true">
        <rect x="0" y="0" width="20" height="14" fill="#c9973f"/>
        <polyline points="0,0 10,8 20,0" fill="none" stroke="#303031" stroke-width="1.6"/>
      </svg>
    </div>

    <div class="divider"></div>

    <div class="phone">
      <svg width="14" height="18" viewBox="0 0 14 18" aria-hidden="true">
        <path d="M4 1 L1 3 C0 8 4 15 10 17 L13 14 L10 11 L8 12 C6 10 5 8 5 6 L7 5 Z" fill="#c9973f"/>
      </svg>
      <span>07822254961</span>
    </div>

    <p class="website">www.renwick-tolliver.co.uk</p>
  </section>
</main>
</body>
</html>
```